Bram Keystone Homes needs a business card

We need a business card for a new company in Canada, Ontario. Our company is all about luxury contraction homes for our clients. Our product and services are custom projects design. Under the business logo that will be created, we want a slogan that will be a memorable phrase for consumers to remember us to tell their friends and relatives.

Additional infomation
- Ludovic Entrasse
- President / Ceo
-519.604.3087

Find point what luxury construction products and services can be done

We like to see colors:
- #663300
- and something other colors or color that would attract the client needs and wants

The final design should communicate leads from new or old clients that will grow our empire. Most of all, we try to work among the budget that clients want

NOTE
- we also need an icon for the business (Example: Instagram, Facebook, and Whatsapp icons)
- We want the company name to be remembered easily for clients and our distributors who would get our orders.
- we need an icon on the business cards: Facebook and Instagram.

Thanks,
Bram Keystone Homes

```html
<!DOCTYPE html>
<html lang="en">
<head>
<meta charset="UTF-8">
<title>Bram Keystone Homes – Business Card</title>
<link href="https://fonts.googleapis.com/css2?family=Work+Sans:wght@400;500;700&display=swap" rel="stylesheet">
<style>
  :root {
    --backdrop: #0e0e0f;
    --card: #1c1c1e;
    --card-edge: #262628;
    --gloss-ink: #4a4a4d;
    --soft-ink: #3a3a3d;
    --light-ink: #d8d8da;
  }
  * { margin: 0; padding: 0; box-sizing: border-box; }
  html, body {
    width: 1200px; height: 900px; overflow: hidden;
    background: var(--backdrop);
    font-family: "Work Sans", Arial, sans-serif;
  }
  .stage {
    position: relative; width: 1200px; height: 900px;
  }
  .card {
    position: absolute; left: 250px; width: 700px; height: 400px;
    background: linear-gradient(135deg, var(--card) 0%, var(--card) 55%, var(--card-edge) 100%);
    box-shadow: 0 10px 30px rgba(0,0,0,0.6);
  }
  .card--front { top: 40px; }
  .card--back { top: 460px; }

  .brand {
    position: absolute; left: 0; right: 0; top: 150px; text-align: center;
  }
  .brand__name {
    font-weight: 700; font-size: 44px; letter-spacing: 0.5px;
    color: var(--gloss-ink);
  }
  .brand__tagline {
    margin-top: 6px; font-weight: 500; font-size: 15px; letter-spacing: 1.6px;
    color: var(--gloss-ink);
  }

  .person {
    position: absolute; right: 390px; top: 150px; text-align: right;
  }
  .person__name {
    font-weight: 500; font-size: 22px; color: var(--soft-ink);
  }
  .person__role {
    margin-top: 4px; font-size: 17px; letter-spacing: 1px; color: var(--soft-ink);
  }
  .divider {
    position: absolute; left: 325px; top: 145px; width: 1px; height: 72px;
    background: var(--gloss-ink);
  }
  .contacts {
    position: absolute; left: 345px; top: 146px; list-style: none;
  }
  .contacts__item {
    display: flex; align-items: center; gap: 10px;
    font-size: 18px; line-height: 24px; letter-spacing: 0.6px;
    color: var(--light-ink);
  }
  .contacts__item svg { width: 13px; height: 13px; flex: none; }
  .address {
    position: absolute; left: 60px; top: 330px;
    font-size: 18px; letter-spacing: 0.8px; color: var(--soft-ink);
  }
</style>
</head>
<body>
<main class="stage">
  <section class="card card--front">
    <div class="brand">
      <div class="brand__name">Bram Keystone Homes</div>
      <div class="brand__tagline">- HOME RENOVATIONS - CUSTOM PROJECT DESIGN -</div>
    </div>
  </section>

  <section class="card card--back">
    <div class="person">
      <div class="person__name">Ludovic Entrasse</div>
      <div class="person__role">President / Ceo</div>
    </div>
    <div class="divider"></div>
    <ul class="contacts">
      <li class="contacts__item">
        <svg viewBox="0 0 24 24" fill="none" stroke="currentColor" stroke-width="2"><path d="M6 3l3 1 1 5-2 1c1 3 3 5 6 6l1-2 5 1 1 3c0 2-2 3-4 3C10 21 3 14 3 7c0-2 1-4 3-4z"/></svg>
        519.604.3087
      </li>
      <li class="contacts__item">
        <svg viewBox="0 0 24 24" fill="none" stroke="currentColor" stroke-width="2"><rect x="3" y="6" width="18" height="12"/><path d="M3 6l9 7 9-7"/></svg>
        info@bramkeystone.com
      </li>
      <li class="contacts__item">
        <svg viewBox="0 0 24 24" fill="none" stroke="currentColor" stroke-width="2"><circle cx="12" cy="12" r="9"/><path d="M3 12h18M12 3c3 3 3 15 0 18M12 3c-3 3-3 15 0 18"/></svg>
        www.bramkeystone.com
      </li>
    </ul>
    <div class="address">3178 Alder Crest Road Brenton, AL 36419</div>
  </section>
</main>
</body>
</html>
```